Business Cards for new orthopaedic surgery practice

My husband and I are starting our own orthopaedic surgery practice. We are looking for a business card that is uniform, but one will have my name/title and the other will have his. You can just create one design with my name on it for now. But when I choose your design as the winning design I will ask that you add another copy with his name/title.

We are looking for classy, simple, elite all in one. We like dark blues/a little gold/yellow. Something that goes with our logo. We want our logo incorporated. Here is all the info you need:
Business name: RV Bone & Vitality Center
Location: 38517 North Willowmere Ave
Maple Harbor, FL 33990
Phone: 954-218-4063
Fax: 954-582-7341
Email: info@myrvbonecare.example

Names: Lydia Vance, M.D.
Board Certified Hand and Upper Extremity Surgeon

Ebo Dansu, M.D.
Board Certified Hip & Knee Replacement/General Orthopaedic Surgeon

Can decide what you want to put on the back. Maybe a slogan:
Built on Trust. Driven by Results

I am just going to upload our logo. The only thing is if we select you as the winning design, the location, and phone numbers may change. We will need your help to update that once fully solidified.

Industry/Entity Type

Medical

Contact Information for Business Card

Colors
0054AA
0677BA
7BADD7
CADEEF
E8F1F8
0094D4
00A9DD
6FCCEA
C7EBF8
E9F6FB

Requirements
Must have
• class, appeal,
Should not have
• We want to air on the side of masculine if we are looking at masculine vs. feminine feel. But we still want it classy, sophisticated, and something we will love

```html
<!DOCTYPE html>
<html lang="en">
<head>
<meta charset="utf-8">
<title>RV Bone &amp; Vitality Center – Business Card</title>
<link rel="stylesheet" href="https://fonts.googleapis.com/css2?family=Cinzel:wght@700&family=Arimo:wght@400&display=swap">
<style>
  :root {
    --navy: #1e2d5c;
    --navy-light: #26365f;
    --navy-deep: #1b2a58;
    --gold: #c9a55a;
    --white: #ffffff;
    --backdrop: #e4e4e4;
  }
  * { box-sizing: border-box; margin: 0; padding: 0; }
  html, body { width: 1200px; height: 1200px; overflow: hidden; }
  body {
    background: var(--backdrop);
    position: relative;
    font-family: "Arimo", Arial, sans-serif;
  }
  .card {
    position: absolute;
    left: 256px;
    width: 688px;
    height: 394px;
    overflow: hidden;
  }
  .card-front { top: 158px; background: var(--white); }
  .card-back {
    top: 653px;
    background: linear-gradient(180deg, var(--navy-light) 0%, var(--navy-deep) 100%);
  }

  /* front */
  .rule { position: absolute; left: 0; width: 100%; height: 3px; background: var(--gold); }
  .rule-top { top: 169px; }
  .rule-bottom { top: 369px; }
  .band {
    position: absolute; left: 0; top: 175px; width: 100%; height: 188px;
    background: var(--navy);
  }
  .practice-name {
    position: absolute; left: 34px; top: 225px; width: 310px;
    display: flex; align-items: center; gap: 14px;
    color: var(--white);
    font-family: "Cinzel", Georgia, serif; font-weight: 700;
    font-size: 25px; line-height: 1.3;
  }
  .practice-dot {
    flex: none; width: 16px; height: 16px; border-radius: 50%;
    background: var(--gold);
  }
  .doctor { position: absolute; left: 398px; top: 52px; }
  .doctor-name {
    font-family: "Cinzel", Georgia, serif; font-weight: 700;
    font-size: 22px; color: var(--navy); letter-spacing: 0.5px;
  }
  .doctor-title {
    margin-top: 4px; font-size: 15px; line-height: 19px; color: var(--gold);
  }
  .address {
    position: absolute; left: 398px; top: 206px;
    color: var(--white); font-size: 16px; line-height: 21px;
  }
  .contacts { position: absolute; left: 398px; top: 261px; list-style: none; }
  .contacts li {
    display: flex; align-items: center; gap: 9px;
    height: 20.5px; color: var(--white); font-size: 16px;
  }
  .contacts svg { width: 14px; height: 14px; flex: none; }

  /* back */
  .emblem {
    position: absolute; left: 241px; top: 80px; width: 206px; height: 206px;
    border: 2px solid var(--gold); border-radius: 50%;
    display: flex; align-items: center; justify-content: center; text-align: center;
    color: var(--white);
    font-family: "Cinzel", Georgia, serif; font-weight: 700;
    font-size: 22px; line-height: 1.3; padding: 0 22px;
  }
  .slogan {
    position: absolute; left: 0; top: 337px; width: 100%; text-align: center;
    color: var(--gold); font-size: 15px; letter-spacing: 3.4px;
  }
</style>
</head>
<body>
  <section class="card card-front">
    <div class="rule rule-top"></div>
    <div class="band"></div>
    <div class="rule rule-bottom"></div>

    <div class="practice-name"><span class="practice-dot"></span><span>RV Bone &amp; Vitality Center</span></div>

    <div class="doctor">
      <h1 class="doctor-name">LYDIA VANCE, M.D.</h1>
      <p class="doctor-title">Board Certified Hand and<br>Upper Extremity Surgeon</p>
    </div>

    <p class="address">38517 North Willowmere Ave<br>Maple Harbor, FL 33990</p>

    <ul class="contacts">
      <li>
        <svg viewBox="0 0 16 16" aria-hidden="true"><path fill="#c9a55a" d="M3.5 1l2.5 3-1.5 1.8c.8 1.8 2.2 3.2 4 4L10.3 8.4l3 2.4-1.3 2.9C6.5 13.7 2.2 9.3 1 3.4z"/></svg>
        954-218-4063
      </li>
      <li>
        <svg viewBox="0 0 16 16" aria-hidden="true"><rect x="4" y="1.5" width="8" height="4" fill="#c9a55a"/><rect x="1" y="6" width="14" height="6" rx="1" fill="#c9a55a"/><rect x="4" y="10" width="8" height="4.5" fill="#c9a55a" stroke="#1e2d5c" stroke-width="1"/></svg>
        954-582-7341
      </li>
      <li>
        <svg viewBox="0 0 16 16" aria-hidden="true"><rect x="1" y="3.5" width="14" height="9" fill="#c9a55a"/><path d="M1.5 4l6.5 5 6.5-5" fill="none" stroke="#1e2d5c" stroke-width="1.2"/></svg>
        info@myrvbonecare.example
      </li>
      <li>
        <svg viewBox="0 0 16 16" aria-hidden="true"><circle cx="8" cy="8" r="6.5" fill="#c9a55a"/><path d="M4 5c2 0 2 2 4 2s1 3 3 3M8 1.5c-1 2 1 3 0 5" fill="none" stroke="#1e2d5c" stroke-width="1.1"/></svg>
        www.myrvbonecare.example
      </li>
    </ul>
  </section>

  <section class="card card-back">
    <div class="emblem">RV Bone &amp; Vitality Center</div>
    <p class="slogan">BUILT ON TRUST. DRIVEN BY RESULTS</p>
  </section>
</body>
</html>
```